New bussiness card, using company logo.
Lionel Brisk
Manager/Director
Brisk Property Developments
Po Box 5347
Marlowe Central
Qld
0491 638 205
lionel@briskpropertydevelopments
eye catching, vibrant colours, professional

```html
<!DOCTYPE html>
<html lang="en">
<head>
<meta charset="utf-8">
<title>Brisk Property Developments – Business Cards</title>
<link rel="stylesheet" href="https://fonts.googleapis.com/css2?family=Jost:wght@400;500;600;700&display=swap">
<style>
  :root {
    --backdrop: #8a5a38;
    --card-white: #ffffff;
    --brand-red: #dc262e;
    --brand-green: #6cbd45;
    --green-light: #8cc63f;
    --ink: #3a3a3a;
    --divider: #9a9a9a;
  }
  * { box-sizing: border-box; margin: 0; padding: 0; }
  html, body { width: 1200px; height: 754px; overflow: hidden; }
  body {
    background: var(--backdrop);
    font-family: "Jost", sans-serif;
    position: relative;
  }
  .card {
    position: absolute;
    width: 525px;
    height: 298px;
    overflow: hidden;
    box-shadow: 0 2px 6px rgba(0,0,0,0.35);
  }
  .card--front  { left: 42px;  top: 38px;  background: var(--card-white); }
  .card--back   { left: 607px; top: 42px;  background: var(--card-white); }
  .card--green  { left: 44px;  top: 397px; background: linear-gradient(180deg, var(--brand-green), var(--green-light)); }
  .card--red    { left: 623px; top: 397px; background: var(--brand-red); }

  .brand-name {
    position: absolute;
    left: 0; right: 0;
    text-align: center;
    font-weight: 700;
    line-height: 1;
    text-transform: uppercase;
  }
  .brand-name__main { display: block; font-size: 56px; letter-spacing: 1px; }
  .brand-name__sub  { display: block; font-size: 22px; letter-spacing: 1.5px; margin-top: 6px; }

  .card--front .brand-name { top: 66px; color: var(--brand-red); }
  .card--back .brand-name  { top: 104px; color: var(--brand-green); }
  .card--back .brand-name .brand-name__main { font-size: 60px; }
  .card--green .brand-name,
  .card--red .brand-name   { top: 132px; color: var(--card-white); }

  .web-address {
    position: absolute;
    left: 0; right: 0;
    text-align: center;
    font-size: 14px;
    letter-spacing: 3px;
    font-weight: 500;
  }
  .card--back .web-address { top: 252px; color: var(--ink); }
  .card--back .web-address .web-address__brisk { color: var(--brand-red); }
  .card--back .web-address .web-address__property { color: var(--brand-green); }
  .card--green .web-address,
  .card--red .web-address { top: 253px; color: var(--card-white); }

  .holder {
    position: absolute;
    right: 305px;
    top: 222px;
    text-align: right;
  }
  .holder__name  { font-size: 19px; font-weight: 600; color: var(--brand-red); line-height: 1.2; }
  .holder__title { font-size: 15px; font-weight: 400; color: var(--brand-green); line-height: 1.3; }

  .divider {
    position: absolute;
    left: 233px;
    top: 198px;
    width: 1px;
    height: 88px;
    background: var(--divider);
  }

  .contacts {
    position: absolute;
    left: 248px;
    top: 202px;
    list-style: none;
    color: var(--ink);
    font-size: 14px;
    line-height: 1.3;
  }
  .contacts li { display: flex; align-items: flex-start; gap: 7px; margin-bottom: 4px; }
  .contacts .contacts__email { font-size: 12.5px; }
  .contacts svg { flex: none; margin-top: 3px; fill: var(--brand-red); }
</style>
</head>
<body>

  <section class="card card--front" aria-label="Business card front">
    <div class="brand-name">
      <span class="brand-name__main">Brisk</span>
      <span class="brand-name__sub">Property Developments</span>
    </div>

    <div class="holder">
      <p class="holder__name">Lionel Brisk</p>
      <p class="holder__title">Manager/Director</p>
    </div>

    <div class="divider"></div>

    <ul class="contacts">
      <li>
        <svg width="10" height="11" viewBox="0 0 10 11" aria-hidden="true"><path d="M2 0.5 L4 3 L3 4.3 C3.6 5.8 4.7 7 6.2 7.6 L7.4 6.6 L9.8 8.6 L8.6 10.5 C4.2 10.2 0.6 6.5 0.3 2 Z"/></svg>
        <span>0491 638 205</span>
      </li>
      <li class="contacts__email">
        <svg width="11" height="8" viewBox="0 0 11 8" aria-hidden="true"><path d="M0 0 H11 V8 H0 Z M0.8 0.8 L5.5 4.6 L10.2 0.8 Z" fill-rule="evenodd"/></svg>
        <span>lionel@briskpropertydevelopments.com</span>
      </li>
      <li>
        <svg width="10" height="10" viewBox="0 0 10 10" aria-hidden="true"><path d="M5 0 L10 4.8 H8.5 V10 H6 V7 H4 V10 H1.5 V4.8 H0 Z"/></svg>
        <span>Po Box 5347<br>Marlowe Central , Qld</span>
      </li>
    </ul>
  </section>

  <section class="card card--back" aria-label="Business card back, white">
    <div class="brand-name">
      <span class="brand-name__main">Brisk</span>
      <span class="brand-name__sub">Property Developments</span>
    </div>
    <p class="web-address">www.<span class="web-address__brisk">brisk</span><span class="web-address__property">propertydevelopments</span>.com</p>
  </section>

  <section class="card card--green" aria-label="Business card, green version">
    <div class="brand-name">
      <span class="brand-name__main">Brisk</span>
      <span class="brand-name__sub">Property Developments</span>
    </div>
    <p class="web-address">www.briskpropertydevelopments.com</p>
  </section>

  <section class="card card--red" aria-label="Business card, red version">
    <div class="brand-name">
      <span class="brand-name__main">Brisk</span>
      <span class="brand-name__sub">Property Developments</span>
    </div>
    <p class="web-address">www.briskpropertydevelopments.com</p>
  </section>

</body>
</html>
```